UI Design for a pre-ordering & Universal loyalty mobile app

We have built a central universal, preordering and gamification mobile app for alot of F&B merchant. The app is called PYRK (Pyrick as in eating something fast). Main goal for this app is too
1. Give users a universal loyalty system where they can accumulate loyalty points and use it on any brands
2. Gives user the ability to preorder for their food or drinks on the app and pick it up instore
3. There will be an E-wallet that is general or there can be a brand e-wallet (where they top-up with the brand only and get extra bonus)
4. There will be promotion such as games, top-up bonuses and rewards.
5. Community app where they can send money or promotion to their friends and will be able to play games together
This app is developed on the Flutter framework and also uses fontawesome font/icon package. Please consider this when doing the UI design for the app.
We are planning to create a mascot for our app as well and when it comes to color and icon, it's not set in stone and we are open for ideas.
I will attached our app icon and a few of our screens for your reference and each page details as follows:
Navigation bar.
There is a navigation bar on the top that should be visible on all screen. On the left will be a button to enter the menu which gives user more option and on the right will be a place for them to scan their QR code for loyalty points or payment and also a button to access their e-wallet.
1. Home screen
This screen is basically the main screen after user login. In this screen there will be
- Main banner (main promotions that's controlled by us)
- Specials banner (smaller) that will be controlled by the store/brands
- Favourite Store or Favourite food/drinks that user pre-configure
2. Shop screen (or can be called something else)
This screen is where they can browse all our participating stores. This screen will include
- Categories (filter)
- Brands which user can click and only view the brand page and stores
- All stores sorted by distances
3. Brand screen
The brand screen gives our brand with multiple store a presense on the app that is branded for them. They can have their own color scheme, logo and will only display their own store
4. Store screen
This will display all the store details, opening time, location, contact information etc.
- This screen will contain a banner/store image
- Store details
- Categories
- Food/drinks within the category
5. Order history screen
This will display their current order or their past order. Not sure if it should be on the main navigation or the sub navigation.
When making the UI design, please work on a color theme that will suit and also consider a mascot design in the future.
Feel free to ask me any questions before proceeding.
Thanks

```html
<!DOCTYPE html>
<html lang="en">
<head>
<meta charset="utf-8">
<title>PYRK – App Screens</title>
<link href="https://fonts.googleapis.com/css2?family=Fjalla+One&family=Open+Sans:wght@400;600&display=swap" rel="stylesheet">
<style>
:root{
  --bg-top:#fde4cb;
  --bg-bottom:#f5b29b;
  --orange:#fca83a;
  --orange-deep:#f76a2c;
  --ink:#3a3a3a;
  --muted:#6b6b6b;
  --screen:#f9f9f9;
  --band:#efefef;
  --nav:#fde0bb;
  --white:#ffffff;
  --brand-blue:#2f7fc1;
  --brand-navy:#2d3f85;
  --brand-lime:#8cc468;
  --brand-green:#2e9b72;
}
*{box-sizing:border-box;margin:0;padding:0}
html,body{width:1200px;height:940px;overflow:hidden}
body{background:linear-gradient(180deg,var(--bg-top),var(--bg-bottom));font-family:"Open Sans",sans-serif;color:var(--ink);position:relative}
.brand-mark{position:absolute;left:0;right:0;top:40px;display:flex;flex-direction:column;align-items:center;gap:10px}
.brand-mark__dot{width:104px;height:104px;border-radius:50%;background:#fbf1e6;border:5px solid #5a2b22}
.brand-mark__name{font-family:"Fjalla One",sans-serif;font-size:48px;color:var(--ink);letter-spacing:1px;line-height:1}
.screen{position:absolute;top:282px;width:254px;height:550px;border-radius:26px;overflow:hidden;background:var(--screen);box-shadow:0 20px 40px rgba(150,70,40,.25);display:flex;flex-direction:column}
.screen--home{left:134px}
.screen--shop{left:489px}
.screen--orders{left:843px}
.topbar{height:55px;background:var(--orange);display:flex;align-items:flex-end;justify-content:space-between;padding:0 14px 10px;flex-shrink:0}
.topbar__title{font-family:"Fjalla One",sans-serif;color:var(--white);font-size:12px}
.topbar__right{display:flex;gap:10px}
.topbar svg{display:block}
.content{flex:1;overflow:hidden}
h2{font-family:"Fjalla One",sans-serif;font-weight:400;font-size:15px;text-align:center;color:var(--ink);letter-spacing:.3px}
.bottomnav{height:38px;background:var(--nav);display:flex;justify-content:space-around;align-items:center;flex-shrink:0}
.bottomnav__item{width:22px;height:22px;border-radius:50%;background:var(--white);display:flex;align-items:center;justify-content:center}
.bottomnav__item--active{background:var(--orange)}
/* home */
.hero{height:123px;background:linear-gradient(110deg,#3a2a20,#5b4030 45%,#2b2420)}
.deals{padding:12px 0 0}
.deal-banner{width:206px;height:103px;margin:10px auto 0;border-radius:4px;background:linear-gradient(100deg,#a6d436 0 60%,#d8202a 60%)}
.dots{display:flex;justify-content:center;gap:6px;margin-top:9px}
.dots span{width:5px;height:5px;border-radius:50%;border:1px solid #9a9a9a}
.dots span.on{background:var(--orange);border-color:var(--orange)}
.favourites{padding:16px 0 0}
.fav-card{position:relative;width:224px;height:118px;margin:10px auto 0;border-radius:3px;background:linear-gradient(160deg,#6b5645,#4a3a30);overflow:hidden}
.fav-card__text{position:absolute;left:16px;bottom:9px;color:var(--white)}
.fav-card__title{font-size:12px}
.fav-card__sub{font-size:9px}
.fav-card__icons{position:absolute;right:12px;top:14px;display:flex;flex-direction:column;gap:7px}
/* search */
.search{background:var(--band);display:flex;align-items:center;gap:12px;padding:15px 16px 17px}
.search__field{flex:1;height:25px;border-radius:13px;background:var(--white);font-size:8px;color:var(--muted);padding:0 10px;display:flex;align-items:center;box-shadow:0 1px 3px rgba(0,0,0,.08)}
.search__btn{width:24px;height:24px;border-radius:50%;background:var(--orange-deep);display:flex;align-items:center;justify-content:center}
.categories{background:var(--white);padding:16px 0 16px}
.chips{display:flex;gap:9px;padding-left:16px;margin-top:10px;white-space:nowrap}
.chip{background:#fdf0e0;border-radius:9px;font-size:9px;padding:2px 12px}
.brands{background:var(--band);padding:15px 0 18px}
.brand-tiles{display:flex;justify-content:center;gap:11px;margin-top:12px}
.brand-tile{width:39px;height:39px;border-radius:3px}
.stores{padding:22px 0 0}
.store{display:flex;gap:18px;padding:0 14px;margin-top:16px}
.store__img{width:56px;height:56px;border-radius:3px;flex-shrink:0}
.store__title{font-size:9.5px}
.pin-line{display:flex;gap:5px;font-size:6.5px;color:var(--muted);margin-top:5px;line-height:1.5}
.store__meta{display:flex;align-items:center;justify-content:space-between;margin-top:7px;font-size:6.5px;color:var(--muted)}
.call{background:var(--orange-deep);color:var(--white);font-size:6.5px;border-radius:8px;padding:3px 8px;display:flex;align-items:center;gap:4px}
/* orders */
.orders{padding:22px 14px 0}
.order{background:var(--white);border:1px solid #ececec;border-radius:4px;padding:7px 8px 10px;margin-top:10px;box-shadow:0 1px 3px rgba(0,0,0,.05)}
.order__head{display:flex;gap:14px}
.order__img{width:28px;height:28px;border-radius:2px;background:linear-gradient(150deg,#c9803a,#4a2c1c);flex-shrink:0}
.order__body{flex:1}
.order__row{display:flex;justify-content:space-between;align-items:center}
.order__title{font-size:9.5px}
.badge{font-size:6.5px;color:#9a9a9a;background:#f1f1f1;border-radius:8px;padding:2px 8px}
.order__foot{border-top:1px solid #eee;margin-top:8px;padding-top:7px;font-size:6.5px;color:var(--muted);line-height:1.9}
.order__foot .order__row{font-size:6.5px}
</style>
</head>
<body>

<header class="brand-mark">
  <div class="brand-mark__dot"></div>
  <div class="brand-mark__name">PYRK</div>
</header>

<!-- shared icon definitions -->
<svg width="0" height="0" style="position:absolute">
  <defs>
    <symbol id="i-menu" viewBox="0 0 16 14"><path d="M1 2h14M1 7h14M1 12h14" stroke="#fff" stroke-width="1.8" stroke-linecap="round"/></symbol>
    <symbol id="i-scan" viewBox="0 0 16 16"><path d="M1 5V1h4M11 1h4v4M15 11v4h-4M5 15H1v-4" fill="none" stroke="#fff" stroke-width="1.8"/></symbol>
    <symbol id="i-wallet" viewBox="0 0 18 16"><rect x="1" y="3" width="16" height="12" rx="2" fill="#fff"/><rect x="11" y="7" width="6" height="4" rx="1" fill="#fca83a"/><path d="M3 3l9-2v2" fill="#fff"/></symbol>
    <symbol id="i-home" viewBox="0 0 16 16"><path d="M8 2L1.5 8h2v6h3.5v-4h2v4H12.5V8h2z" fill="currentColor"/></symbol>
    <symbol id="i-cart" viewBox="0 0 16 16"><path d="M1 2h2.5l2 8h7.5l1.5-6H4.5" fill="none" stroke="currentColor" stroke-width="1.6"/><circle cx="6.5" cy="13" r="1.3" fill="currentColor"/><circle cx="12" cy="13" r="1.3" fill="currentColor"/></symbol>
    <symbol id="i-receipt" viewBox="0 0 16 16"><path d="M4 1h9v14l-2-1.5-2 1.5-2-1.5-2 1.5z" fill="currentColor"/><path d="M6 5h5M6 8h5" stroke="#fff" stroke-width="1.2"/></symbol>
    <symbol id="i-game" viewBox="0 0 18 14"><path d="M4 2h10c2 0 3.5 2 3.5 6s-1.5 5-3 4l-2-2H5.5l-2 2c-1.5 1-3-0-3-4S2 2 4 2z" fill="currentColor"/><path d="M4 7h4M6 5v4" stroke="#fff" stroke-width="1.3"/><circle cx="12.5" cy="6" r="1" fill="#fff"/><circle cx="14" cy="8" r="1" fill="#fff"/></symbol>
    <symbol id="i-search" viewBox="0 0 16 16"><circle cx="7" cy="7" r="4.5" fill="none" stroke="#fff" stroke-width="1.8"/><path d="M10.5 10.5L14 14" stroke="#fff" stroke-width="1.8" stroke-linecap="round"/></symbol>
    <symbol id="i-pin" viewBox="0 0 10 12"><path d="M5 0.5a4 4 0 0 0-4 4c0 3 4 7 4 7s4-4 4-7a4 4 0 0 0-4-4z" fill="#f76a2c"/><circle cx="5" cy="4.5" r="1.5" fill="#fff"/></symbol>
    <symbol id="i-phone" viewBox="0 0 12 12"><path d="M2.5 1l2 2.5-1 1.3c.7 1.5 1.9 2.7 3.4 3.4l1.3-1 2.5 2-1 2C5 11 1 7 .5 2.5z" fill="#fff"/></symbol>
    <symbol id="i-star" viewBox="0 0 12 12"><path d="M6 .5l1.7 3.5 3.8.5-2.8 2.7.7 3.8L6 9.2 2.6 11l.7-3.8L.5 4.5l3.8-.5z" fill="#fff"/></symbol>
    <symbol id="i-pin-white" viewBox="0 0 10 12"><path d="M5 0.5a4 4 0 0 0-4 4c0 3 4 7 4 7s4-4 4-7a4 4 0 0 0-4-4z" fill="none" stroke="#fff" stroke-width="1.2"/><circle cx="5" cy="4.5" r="1.4" fill="#fff"/></symbol>
  </defs>
</svg>

<!-- Home screen -->
<section class="screen screen--home">
  <div class="topbar">
    <svg width="15" height="13"><use href="#i-menu"/></svg>
    <span class="topbar__title">PYRK</span>
    <div class="topbar__right">
      <svg width="14" height="14"><use href="#i-scan"/></svg>
      <svg width="16" height="14"><use href="#i-wallet"/></svg>
    </div>
  </div>
  <div class="content">
    <div class="hero" role="img" aria-label="Main promotion banner: photo of an iced caramel drink with the headline Perfect Brew"></div>
    <div class="deals">
      <h2>DEALS</h2>
      <div class="deal-banner" role="img" aria-label="Store special banner: coconut jelly and premium boba pearl toppings"></div>
      <div class="dots"><span class="on"></span><span></span><span></span><span></span></div>
    </div>
    <div class="favourites">
      <h2>FAVOURITES</h2>
      <div class="fav-card" role="img" aria-label="Favourite store: photo of a warm café interior">
        <div class="fav-card__icons">
          <svg width="10" height="10"><use href="#i-star"/></svg>
          <svg width="9" height="11"><use href="#i-pin-white"/></svg>
        </div>
        <div class="fav-card__text">
          <div class="fav-card__title">Lorem Ipsum</div>
          <div class="fav-card__sub">Lorem ipsum dolor sit amet, consecte</div>
        </div>
      </div>
    </div>
  </div>
  <nav class="bottomnav">
    <span class="bottomnav__item bottomnav__item--active" style="color:#fff"><svg width="12" height="12"><use href="#i-home"/></svg></span>
    <span class="bottomnav__item" style="color:var(--orange)"><svg width="12" height="12"><use href="#i-cart"/></svg></span>
    <span class="bottomnav__item" style="color:var(--orange)"><svg width="12" height="12"><use href="#i-receipt"/></svg></span>
    <span class="bottomnav__item" style="color:var(--orange)"><svg width="13" height="11"><use href="#i-game"/></svg></span>
  </nav>
</section>

<!-- Shop screen -->
<section class="screen screen--shop">
  <div class="topbar">
    <svg width="15" height="13"><use href="#i-menu"/></svg>
    <span class="topbar__title">PYRK</span>
    <div class="topbar__right">
      <svg width="14" height="14"><use href="#i-scan"/></svg>
      <svg width="16" height="14"><use href="#i-wallet"/></svg>
    </div>
  </div>
  <div class="content">
    <div class="search">
      <div class="search__field">Search</div>
      <div class="search__btn"><svg width="11" height="11"><use href="#i-search"/></svg></div>
    </div>
    <div class="categories">
      <h2>CATEGORIES</h2>
      <div class="chips"><span class="chip">Tea</span><span class="chip">Bubble Tea</span><span class="chip">Coffee</span><span class="chip">Snacks</span></div>
    </div>
    <div class="brands">
      <h2>BRANDS</h2>
      <div class="brand-tiles">
        <span class="brand-tile" style="background:var(--brand-blue)"></span>
        <span class="brand-tile" style="background:var(--brand-navy)"></span>
        <span class="brand-tile" style="background:var(--brand-lime)"></span>
        <span class="brand-tile" style="background:var(--brand-green)"></span>
      </div>
    </div>
    <div class="stores">
      <h2>STORES NEAR YOU</h2>
      <div class="store">
        <div class="store__img" role="img" aria-label="Store photo: restaurant interior with warm lights" style="background:linear-gradient(150deg,#d08a3c,#5a2f1a)"></div>
        <div style="flex:1">
          <div class="store__title">Lorem Ipsum</div>
          <div class="pin-line"><svg width="6" height="8"><use href="#i-pin"/></svg><span>Lorem ipsum dolor sit amet,<br>consectetur adipiscing elit</span></div>
          <div class="store__meta"><span>5 min &nbsp;|&nbsp; 1.24 Kms</span><span class="call"><svg width="7" height="7"><use href="#i-phone"/></svg>+1 555-0142</span></div>
        </div>
      </div>
      <div class="store">
        <div class="store__img" role="img" aria-label="Store photo: outdoor café terrace with plants" style="background:linear-gradient(150deg,#7fa660,#b9815b)"></div>
        <div style="flex:1">
          <div class="store__title">Lorem Ipsum</div>
          <div class="pin-line"><svg width="6" height="8"><use href="#i-pin"/></svg><span>Lorem ipsum dolor sit amet,<br>consectetur adipiscing elit</span></div>
          <div class="store__meta"><span>5 min &nbsp;|&nbsp; 1.24 Kms</span><span class="call"><svg width="7" height="7"><use href="#i-phone"/></svg>+1 555-0142</span></div>
        </div>
      </div>
    </div>
  </div>
  <nav class="bottomnav">
    <span class="bottomnav__item bottomnav__item--active" style="color:#fff"><svg width="12" height="12"><use href="#i-home"/></svg></span>
    <span class="bottomnav__item" style="color:var(--orange)"><svg width="12" height="12"><use href="#i-cart"/></svg></span>
    <span class="bottomnav__item" style="color:var(--orange)"><svg width="12" height="12"><use href="#i-receipt"/></svg></span>
    <span class="bottomnav__item" style="color:var(--orange)"><svg width="13" height="11"><use href="#i-game"/></svg></span>
  </nav>
</section>

<!-- Orders screen -->
<section class="screen screen--orders">
  <div class="topbar">
    <svg width="15" height="13"><use href="#i-menu"/></svg>
    <span class="topbar__title">PYRK</span>
    <div class="topbar__right">
      <svg width="14" height="14"><use href="#i-scan"/></svg>
      <svg width="16" height="14"><use href="#i-wallet"/></svg>
    </div>
  </div>
  <div class="content">
    <div class="search">
      <div class="search__field">Search</div>
      <div class="search__btn"><svg width="11" height="11"><use href="#i-search"/></svg></div>
    </div>
    <div class="orders">
      <h2>YOUR ORDERS</h2>
      <article class="order">
        <div class="order__head">
          <div class="order__img" role="img" aria-label="Store thumbnail photo"></div>
          <div class="order__body">
            <div class="order__row"><span class="order__title">Lorem Ipsum</span><span class="badge">Delivered</span></div>
            <div class="pin-line"><svg width="6" height="8"><use href="#i-pin"/></svg><span>Lorem ipsum dolor sit amet,<br>consectetur adipiscing elit</span></div>
          </div>
        </div>
        <div class="order__foot">
          <div>1 x Lorem Ipsum</div>
          <div class="order__row"><span>10 Oct 2023 at 19:10</span><span>$ 57.85</span></div>
        </div>
      </article>
      <article class="order">
        <div class="order__head">
          <div class="order__img" role="img" aria-label="Store thumbnail photo"></div>
          <div class="order__body">
            <div class="order__row"><span class="order__title">Lorem Ipsum</span><span class="badge">Delivered</span></div>
            <div class="pin-line"><svg width="6" height="8"><use href="#i-pin"/></svg><span>Lorem ipsum dolor sit amet,<br>consectetur adipiscing elit</span></div>
          </div>
        </div>
        <div class="order__foot">
          <div>1 x Lorem Ipsum</div>
          <div class="order__row"><span>10 Oct 2023 at 19:10</span><span>$ 57.85</span></div>
        </div>
      </article>
      <article class="order">
        <div class="order__head">
          <div class="order__img" role="img" aria-label="Store thumbnail photo"></div>
          <div class="order__body">
            <div class="order__row"><span class="order__title">Lorem Ipsum</span><span class="badge">Delivered</span></div>
            <div class="pin-line"><svg width="6" height="8"><use href="#i-pin"/></svg><span>Lorem ipsum dolor sit amet,<br>consectetur adipiscing elit</span></div>
          </div>
        </div>
        <div class="order__foot">
          <div>1 x Lorem Ipsum</div>
          <div class="order__row"><span>10 Oct 2023 at 19:10</span><span>$ 57.85</span></div>
        </div>
      </article>
    </div>
  </div>
  <nav class="bottomnav">
    <span class="bottomnav__item bottomnav__item--active" style="color:#fff"><svg width="12" height="12"><use href="#i-home"/></svg></span>
    <span class="bottomnav__item" style="color:var(--orange)"><svg width="12" height="12"><use href="#i-cart"/></svg></span>
    <span class="bottomnav__item" style="color:var(--orange)"><svg width="12" height="12"><use href="#i-receipt"/></svg></span>
    <span class="bottomnav__item" style="color:var(--orange)"><svg width="13" height="11"><use href="#i-game"/></svg></span>
  </nav>
</section>

</body>
</html>
```